New web design for a service provider in the medical field

We are looking for a new design for our website. We are a company that repairs and sells medical endoscopes. Our customers include doctors and hospitals. Our current website can be found at https://lumavex.de/en/lumavex-english.
We need a new web design (without programming) for the following 3 pages:
-Startpage https://lumavex.de/en/lumavex-english/
-Used endoscopes https://lumavex.de/en/used-endoscopes/
-Purchase https://lumavex.de/en/purchase/
The design should be modern and stylish.
The blue color of the logo should be reflected on the page, but not too intrusive.
I have uploaded the images from the header. If more images are needed, let me know and I will upload them.

Target Market(s)
Doctors and hospitals

```html
<!DOCTYPE html>
<html lang="en">
<head>
<meta charset="utf-8">
<title>Lumavex – Endoscope Repair</title>
<link href="https://fonts.googleapis.com/css2?family=Montserrat:wght@400;500;600;700&display=swap" rel="stylesheet">
<style>
:root{
  --navy:#1d3a52;
  --navy-dark:#18324a;
  --blue:#2ba3df;
  --blue-light:#53bdf0;
  --ice:#eaf2f8;
  --text:#2a3440;
  --muted:#6b7785;
  --white:#fff;
}
*{margin:0;padding:0;box-sizing:border-box}
html,body{width:1200px;height:5017px;overflow:hidden}
body{font-family:'Montserrat',sans-serif;color:var(--text);background:var(--white);position:relative}
.abs{position:absolute}
.btn{display:inline-flex;align-items:center;justify-content:center;border-radius:24px;font-size:12px;font-weight:600;text-transform:uppercase;letter-spacing:.3px}
.img-fill{background:radial-gradient(circle at 45% 40%,#f4f7fa 0%,#c9d4de 55%,#8797a6 100%)}
.brand{font-weight:600;font-size:22px;color:var(--navy);display:flex;align-items:center;gap:8px}
.brand .dot{width:10px;height:10px;border-radius:50%;background:var(--blue)}

/* header */
.topbar{top:0;left:0;width:1200px;height:107px;background:var(--white)}
.contact-pill{top:0;left:690px;width:400px;height:40px;background:var(--blue);border-radius:0 0 0 22px;color:#fff;font-size:11px;font-weight:600;display:flex;align-items:center;gap:24px;padding-left:22px}
.contact-pill span{display:flex;align-items:center;gap:7px}
.nav{top:66px;left:305px;display:flex;gap:30px;font-size:11.5px;font-weight:700;color:var(--navy)}
.nav a{color:inherit;text-decoration:none;padding-bottom:6px}
.nav a.active{border-bottom:2px solid var(--blue)}

/* hero */
.hero{top:107px;left:0;width:1200px;height:590px;background:linear-gradient(120deg,#1f3b54 0%,#2b5575 60%,#3f6d8e 100%)}
.hero-kicker{top:285px;left:105px;color:#fff;font-size:21px;letter-spacing:1.5px}
.hero-title{top:315px;left:105px;font-size:35px;font-weight:600;line-height:1.2;color:#fff}
.hero-title em{font-style:normal;color:var(--blue-light)}
.hero-btn{top:423px;left:104px;width:165px;height:44px;background:var(--blue);color:#fff}

/* intro */
.intro-title{top:812px;left:0;width:1200px;text-align:center;font-size:35px;font-weight:500;color:var(--navy)}
.intro-title em{font-style:normal;color:var(--blue)}
.intro-text{top:895px;left:250px;width:700px;text-align:center;font-size:19px;line-height:1.7;color:var(--text)}

/* about band */
.about-title{top:1226px;left:616px;width:470px;font-size:25px;font-weight:500;color:#fff;line-height:1.25}
.about-text{top:1340px;left:618px;width:460px;font-size:14.5px;line-height:1.6;color:#e4edf4}
.about-text p{margin-bottom:14px}

/* service cards */
.card{top:1780px;width:334px;height:280px;border:1.5px solid #9fd3ee;border-radius:6px;background:#fff;text-align:center;padding-top:70px}
.card.featured{background:var(--blue);border-color:var(--blue);color:#fff}
.card .icon{position:absolute;top:-50px;left:117px;width:100px;height:100px;border-radius:50%;background:var(--blue);border:8px solid #fff;box-shadow:0 0 0 2px #9fd3ee;display:flex;align-items:center;justify-content:center}
.card.featured .icon{background:var(--navy)}
.card h3{font-size:21px;font-weight:500;color:var(--navy)}
.card.featured h3{color:#fff}
.card h4{font-size:16px;font-weight:500;margin-top:6px;color:var(--navy)}
.card.featured h4{color:#fff}
.card p{font-size:10.5px;line-height:1.75;margin:8px auto 0;width:270px}
.card .btn{margin-top:16px;width:138px;height:38px;border:2px solid var(--navy);color:var(--navy)}
.card.featured .btn{border-color:#fff;color:#fff}

/* faulty */
.faulty{top:2080px;left:0;width:1200px;height:547px;background:linear-gradient(180deg,#f7fafc 0%,#e3edf4 100%)}
.faulty-title{top:2205px;left:130px;font-size:34px;font-weight:500;color:var(--navy)}
.faulty-title em{font-style:normal;color:var(--blue)}
.faulty-sub{top:2280px;left:131px;font-size:21px;color:var(--text)}
.faulty-text{top:2320px;left:131px;width:460px;font-size:17px;line-height:1.65}
.faulty-btn{top:2462px;left:133px;width:168px;height:46px;background:var(--navy);color:#fff}

/* outcome */
.outcome-title{top:2680px;left:0;width:1200px;text-align:center;font-size:30px;font-weight:500;color:var(--navy)}
.outcome-title em{font-style:normal;color:var(--blue)}
.outcome-rule{top:2728px;left:572px;width:56px;height:2px;background:var(--blue)}
.feature{width:314px;height:238px;border:1.5px solid #b5ddf2;border-radius:42px 6px 42px 6px;padding:36px 36px 0;background:#fff}
.feature.hl{background:linear-gradient(135deg,#2ba3df,#5cc2f0);border-color:transparent;color:#fff}
.feature svg{display:block;margin-bottom:18px}
.feature h5{font-size:17px;font-weight:700;color:var(--navy);line-height:1.2}
.feature.hl h5{color:#fff}
.feature p{font-size:13.5px;line-height:1.5;margin-top:10px;color:var(--muted)}
.feature.hl p{color:#e8f6fd}

/* decision */
.decision{top:3354px;left:0;width:1200px;height:640px;background:var(--navy)}
.decision-title{top:3410px;left:0;width:1200px;text-align:center;font-size:27px;font-weight:500;color:#fff;line-height:1.2}
.point{width:300px;color:#fff}
.point h6{font-size:13px;font-weight:700}
.point p{font-size:9.5px;line-height:1.6;color:#c9d7e2;margin-top:4px}
.point.left{text-align:right}
.pico{width:56px;height:56px;border-radius:50%;border:2px solid #6fa5c9;background:var(--navy);display:flex;align-items:center;justify-content:center}
.pico svg{width:28px;height:28px;fill:none;stroke:#fff;stroke-width:1.6;stroke-linecap:round;stroke-linejoin:round}
.hub{top:3558px;left:478px;width:272px;height:272px;border-radius:50%;background:#fff;border:10px solid #2f5878;display:flex;align-items:center;justify-content:center}
.decision-btn{top:3905px;left:500px;width:275px;height:46px;background:var(--blue);color:#fff;text-transform:none;font-size:13px}

/* contact */
.contact{top:3994px;left:0;width:1200px;height:671px;background:linear-gradient(180deg,#fff 0%,#e6eff6 100%)}
.help{top:4130px;left:131px;width:340px;height:410px;background:linear-gradient(135deg,#2ba3df,#59c0f0);border-radius:50px 0 0 0;color:#fff;text-align:right;padding:68px 36px 0 0}
.help small{font-size:13px;font-weight:500;letter-spacing:.5px}
.help h2{font-size:29px;font-weight:500;line-height:1.2;margin-top:4px}
.help p{font-size:13.5px;line-height:1.55;margin-top:24px;margin-left:40px}
.form-frame{top:4143px;left:727px;width:325px;height:440px;border:3px solid var(--navy);border-bottom:none;border-left:none}
.form{top:4175px;left:464px;width:588px;height:408px;background:#fff;box-shadow:0 8px 30px rgba(29,58,82,.12);padding:46px 48px}
.form h3{font-size:18px;font-weight:500;color:var(--navy)}
.field{position:absolute;width:240px}
.field label{display:block;font-size:12.5px;font-weight:600;color:var(--navy)}
.field div{font-size:11px;color:#99a4ae;border-bottom:1px solid #dbe2e8;padding:10px 0}
.send{top:4465px;left:935px;width:62px;height:62px;border-radius:50%;background:var(--navy);display:flex;align-items:center;justify-content:center}

/* footer */
.footer{top:4665px;left:0;width:1200px;height:352px;background:var(--navy-dark);color:#fff}
.fcol{top:4720px;color:#fff}
.fcol h6{font-size:13.5px;font-weight:700;color:#fff;border-left:3px solid var(--blue);padding-left:18px;height:22px;line-height:22px}
.fcol ul{list-style:none;margin-top:14px;padding-left:21px}
.fcol li{font-size:13px;line-height:29px;color:#d4dfe8}
.social{display:flex;gap:8px;margin:14px 0 0 21px}
.social span{width:28px;height:28px;border-radius:50%;background:#fff}
.footer-text{top:4858px;left:122px;width:270px;font-size:11.5px;line-height:1.4;color:#a9bccb}
.copy{top:4963px;left:0;width:1200px;text-align:center;font-size:12px;color:#a9bccb;border-top:1px solid #2d4a62;padding-top:18px}
</style>
</head>
<body>

<!-- header -->
<header class="abs topbar">
  <div class="abs brand" style="top:36px;left:106px">Lumavex <span class="dot"></span></div>
  <div class="abs contact-pill">
    <span><svg width="14" height="14" viewBox="0 0 14 14"><rect x="1" y="3" width="12" height="8" rx="1" fill="none" stroke="#fff" stroke-width="1.4"/><path d="M1 3l6 5 6-5" fill="none" stroke="#fff" stroke-width="1.4"/></svg>info@lumavex.de</span>
    <span><svg width="14" height="14" viewBox="0 0 14 14"><path d="M3 1l3 3-1.5 1.5a8 8 0 004 4L10 8l3 3-2 2C6 13 1 8 1 3z" fill="#fff"/></svg>+49 4100 555 120-0</span>
    <span>ENG ▾</span>
  </div>
  <nav class="abs nav">
    <a class="active">ENDOSCOPE REPAIR</a><a>ENDOSCOPY SYSTEMS</a><a>ENDOSCOPY ACCESSORIES</a><a>ACCESSORIES CATALOG</a><a>PURCHASE</a>
  </nav>
</header>

<!-- hero -->
<section class="abs hero"></section>
<svg class="abs" style="top:560px;left:0" width="1200" height="180" viewBox="0 0 1200 180">
  <path d="M0 40 C300 140 650 70 900 60 C1050 55 1150 40 1200 20 V180 H0Z" fill="#fff"/>
  <path d="M0 50 C300 150 650 80 900 70 C1050 65 1150 50 1200 30" fill="none" stroke="var(--blue)" stroke-width="5"/>
  <circle cx="602" cy="126" r="36" fill="#fff" stroke="#9fd3ee" stroke-width="2"/>
  <path d="M602 110v30M592 130l10 10 10-10" fill="none" stroke="var(--blue)" stroke-width="2.5"/>
</svg>
<svg class="abs" style="top:150px;left:590px" width="500" height="460" viewBox="0 0 500 460">
  <path d="M120 420 A230 230 0 1 1 440 330" fill="none" stroke="var(--blue)" stroke-width="16"/>
</svg>
<div class="abs img-fill" role="img" aria-label="Photo of a flexible endoscope control handle" style="top:170px;left:613px;width:440px;height:420px;border-radius:50%"></div>
<div class="abs hero-kicker">WELCOME TO LUMAVEX</div>
<h1 class="abs hero-title">PUT YOUR ENDOSCOPE<br><em>IN RELIABLE HANDS!</em></h1>
<a class="abs btn hero-btn">LEARN MORE</a>

<!-- intro -->
<h2 class="abs intro-title">YOUR FUTURE <em>OUR SERVICE</em></h2>
<p class="abs intro-text">Lumavex GmbH is specialised in the repair and sale of Orvanta, Pellix and Fujara flexible medical endoscopes. As a service-oriented company, we are at your side with our knowledge and skills!</p>

<!-- about band -->
<svg class="abs" style="top:1050px;left:0" width="1200" height="660" viewBox="0 0 1200 660">
  <path d="M0 0 C250 90 550 110 1200 40 V560 C950 660 700 540 400 590 C250 615 100 600 0 570Z" fill="var(--navy)"/>
  <path d="M0 0 C250 90 550 110 1200 40 V58 C550 128 250 108 0 22Z" fill="var(--blue)"/>
</svg>
<div class="abs" style="top:1185px;left:118px;width:430px;height:430px;border-radius:50%;border:3px solid var(--blue)"></div>
<div class="abs img-fill" role="img" aria-label="Photo of an endoscope handpiece with cable" style="top:1210px;left:143px;width:380px;height:380px;border-radius:50%"></div>
<h2 class="abs about-title">Endoscope repairs and second hand endoscopes from Lumavex cause the outcome matters!</h2>
<div class="abs about-text">
  <p>Lumavex is a privileged partner for the start-up facility or optimisation of existing healthcare facilities, doctor's offices and hospitals. The quality and reliability of our products and our offered service are our best advertisement!</p>
  <p>As a result of optimised processes and highly qualified specialists in our company, we can work very quickly and with high quality for your benefit of least possible restrictions in your doctor's office or in your hospital.</p>
</div>

<!-- service cards -->
<div class="abs card" style="left:99px">
  <div class="icon"><svg width="44" height="44" viewBox="0 0 44 44" fill="none" stroke="#fff" stroke-width="2"><circle cx="16" cy="22" r="12"/><circle cx="16" cy="22" r="6"/><path d="M28 18h12v8H28"/></svg></div>
  <h3>REPAIR</h3><h4>Endoscope repair service</h4>
  <p>Manufacturer-independent we repair and maintain endoscopes, individual components</p>
  <a class="btn">LEARN MORE</a>
</div>
<div class="abs card featured" style="left:450px">
  <div class="icon"><svg width="44" height="44" viewBox="0 0 44 44" fill="none" stroke="#fff" stroke-width="2"><circle cx="18" cy="16" r="9"/><path d="M18 25v12M12 40h12M26 12l10-6"/></svg></div>
  <h3>SALE</h3><h4>Used endoscopes</h4>
  <p>Our regular stock includes refurbished gastroscopes, colonoscopes, bronchoscopes, cystoscopes and duodenoscopes from the well-known manufacturers Orvanta, Pellix and Fujara.</p>
  <a class="btn">LEARN MORE</a>
</div>
<div class="abs card" style="left:801px">
  <div class="icon"><svg width="44" height="44" viewBox="0 0 44 44" fill="none" stroke="#fff" stroke-width="2"><rect x="14" y="6" width="14" height="20" rx="3"/><path d="M21 26v12M16 40h10M28 12h6"/></svg></div>
  <h3>PURCHASE</h3><h4>Used endoscopes</h4>
  <p>We are very interested in buying your old endoscopes – even defective and dismantled! We offer fair conditions! Please contact us for a purchase offer!</p>
  <a class="btn">LEARN MORE</a>
</div>

<!-- faulty -->
<section class="abs faulty"></section>
<svg class="abs" style="top:2100px;left:640px" width="520" height="500" viewBox="0 0 520 500">
  <path d="M60 160 A230 230 0 0 1 470 120" fill="none" stroke="var(--blue)" stroke-width="16"/>
</svg>
<div class="abs" style="top:2110px;left:660px;width:470px;height:470px;border-radius:50%;border:2px solid var(--blue)"></div>
<div class="abs img-fill" role="img" aria-label="Photo of an endoscope control body close-up" style="top:2125px;left:675px;width:440px;height:440px;border-radius:50%"></div>
<h2 class="abs faulty-title">FAULTY <em>ENDOSCOPE?</em></h2>
<p class="abs faulty-sub">We ensure quick and smooth repairs!</p>
<p class="abs faulty-text">Lorem ipsum dolor sit amet, consectetur adipiscing elit, sed do eiusmod tempor incididunt ut labore et dolore magna aliqua. Ut enim ad minim veniam, quis nostrud exercitation ullamco laboris.</p>
<a class="abs btn faulty-btn">PICK UP ORDER</a>

<!-- outcome -->
<h2 class="abs outcome-title">CAUSE THE <em>OUTCOME MATTERS</em></h2>
<div class="abs outcome-rule"></div>
<div class="abs feature hl" style="top:2766px;left:134px">
  <svg width="44" height="44" viewBox="0 0 44 44" fill="none" stroke="#fff" stroke-width="1.8"><circle cx="22" cy="22" r="8"/><circle cx="22" cy="6" r="3"/><circle cx="22" cy="38" r="3"/><circle cx="7" cy="22" r="3"/><circle cx="37" cy="22" r="3"/></svg>
  <h5>One company for<br>everyone</h5><p>We are a service provider for doctors and hospitals!</p>
</div>
<div class="abs feature" style="top:2773px;left:462px">
  <svg width="50" height="50" viewBox="0 0 50 50" fill="none" stroke="var(--navy)" stroke-width="1.8"><circle cx="16" cy="20" r="6"/><circle cx="34" cy="20" r="6"/><path d="M5 42c0-8 5-12 11-12s11 4 11 12M23 42c0-8 5-12 11-12s11 4 11 12"/></svg>
  <h5>Experience<br>characterises us</h5><p>Our team has many years of experience in the business field!</p>
</div>
<div class="abs feature" style="top:2773px;left:789px">
  <svg width="40" height="56" viewBox="0 0 40 56" fill="none" stroke="var(--navy)" stroke-width="1.8"><rect x="8" y="10" width="16" height="22" rx="3"/><path d="M16 32v18M24 16h8v-12"/></svg>
  <h5>The product is close<br>to our hearts</h5><p>We repair and sell second hand, flexible endoscopes!</p>
</div>
<div class="abs feature" style="top:3020px;left:144px">
  <svg width="42" height="50" viewBox="0 0 42 50" fill="none" stroke="var(--navy)" stroke-width="1.8"><path d="M21 3l16 6v14c0 12-8 20-16 24C13 43 5 35 5 23V9z"/><path d="M14 24l5 5 9-10" stroke="var(--blue)"/></svg>
  <h5>Guaranteed service</h5><p>You receive a six-month warranty on all repairs!</p>
</div>
<div class="abs feature" style="top:3024px;left:470px">
  <svg width="56" height="50" viewBox="0 0 56 50" fill="none" stroke="var(--navy)" stroke-width="1.8"><path d="M28 4l4 8 9 1-6 6 2 9-9-5-8 5 2-9-6-6 9-1z"/><path d="M4 40h12l10 4 22-8" stroke="var(--blue)"/></svg>
  <h5>Quality not quantity</h5><p>Reliability and durability instead of inferior replacements!</p>
</div>
<div class="abs feature" style="top:3024px;left:797px">
  <svg width="50" height="52" viewBox="0 0 50 52" fill="none" stroke="var(--navy)" stroke-width="1.8"><path d="M20 3l15 6v12c0 10-7 17-15 21C12 38 5 31 5 21V9z"/><circle cx="34" cy="36" r="8" stroke="var(--blue)"/></svg>
  <h5>Services for everyone</h5><p>Our service includes the manufacturers Orvanta, Pellix and Fujara!</p>
</div>

<!-- decision -->
<section class="abs decision"></section>
<h2 class="abs decision-title">LUMAVEX GMBH, YOUR DECISION<br>FOR YOUR FUTURE</h2>
<svg class="abs" style="top:3500px;left:420px" width="390" height="390" viewBox="0 0 390 390">
  <circle cx="195" cy="195" r="175" fill="none" stroke="#3a6283" stroke-width="2" stroke-dasharray="4 6"/>
</svg>
<div class="abs hub"><div class="brand" style="font-size:24px">Lumavex <span class="dot"></span></div></div>

<div class="abs point left" style="top:3555px;left:128px"><h6>Fast Repairs</h6><p>Keep potential disruptions in your doctor's office or in your hospital at minimum</p></div>
<div class="abs pico" style="top:3548px;left:448px"><svg viewBox="0 0 28 28"><path d="M5 23l10-10M17 5a5 5 0 006 6l-3 3-6-6z"/><path d="M5 5l6 6M20 20l3 3M8 5l-3 3"/></svg></div>

<div class="abs point left" style="top:3672px;left:98px"><h6>On-site service</h6><p>We will gladly pay you a visit to to carry out analysis and repairs on site. Due to our many years of experience</p></div>
<div class="abs pico" style="top:3670px;left:405px"><svg viewBox="0 0 28 28"><circle cx="14" cy="14" r="4"/><path d="M14 3v4M14 21v4M3 14h4M21 14h4M6 6l3 3M19 19l3 3M22 6l-3 3M9 19l-3 3"/></svg></div>

<div class="abs point left" style="top:3800px;left:118px"><h6>Without a maintenance contract</h6><p>No subscription or other maintenance contract, but one-time and sustainable repair work</p></div>
<div class="abs pico" style="top:3790px;left:435px"><svg viewBox="0 0 28 28"><rect x="6" y="5" width="16" height="19" rx="2"/><path d="M11 3h6v4h-6zM10 12h8M10 16h8M10 20h5"/></svg></div>

<div class="abs pico" style="top:3548px;left:730px"><svg viewBox="0 0 28 28"><circle cx="14" cy="12" r="7"/><path d="M14 8v8M12 10h3a1.5 1.5 0 010 3h-2a1.5 1.5 0 000 3h3"/><path d="M4 24h20"/></svg></div>
<div class="abs point" style="top:3555px;left:810px"><h6>Highly cost efficient</h6><p>Benefit from our first class recommendations and implementation by our experienced staff.</p></div>

<div class="abs pico" style="top:3670px;left:777px"><svg viewBox="0 0 28 28"><rect x="10" y="4" width="8" height="10" rx="2"/><path d="M14 14v5M4 20h6l4 3 10-4"/></svg></div>
<div class="abs point" style="top:3665px;left:848px"><h6>Loan equipment service</h6><p>We will gladly pay you a visit to to carry out analysis and repairs on site. Due to our many years of experience</p></div>

<div class="abs pico" style="top:3790px;left:740px"><svg viewBox="0 0 28 28"><path d="M14 4l3 6 6 1-4.5 4 1 6-5.5-3-5.5 3 1-6L5 11l6-1z"/></svg></div>
<div class="abs point" style="top:3800px;left:810px"><h6>First class service</h6><p>Our clients always come first!</p></div>

<svg class="abs" style="top:3880px;left:0" width="1200" height="130" viewBox="0 0 1200 130">
  <path d="M0 40 C200 -10 400 60 700 50 C900 44 1050 10 1200 0 V130 H0Z" fill="#fff"/>
  <path d="M0 40 C200 -10 400 60 700 50 C900 44 1050 10 1200 0" fill="none" stroke="var(--blue)" stroke-width="5"/>
</svg>
<a class="abs btn decision-btn">Learn more about Lumavex</a>

<!-- contact -->
<section class="abs contact"></section>
<div class="abs form-frame"></div>
<div class="abs help"><small>CONTACT US</small><h2>HOW CAN WE<br>HELP YOU?</h2><p>Use the contact form below or the possibility of contacting us by post, telephone or email!</p></div>
<div class="abs form">
  <h3>LEAVE US A MESSAGE</h3>
  <div class="field" style="top:116px;left:54px"><label>Your Name</label><div>John Smith</div></div>
  <div class="field" style="top:116px;left:312px"><label>Company</label><div>Lorem ipsum dolor sit amet</div></div>
  <div class="field" style="top:202px;left:54px"><label>Email Address</label><div>John.Smith@mail.com</div></div>
  <div class="field" style="top:202px;left:312px"><label>Phone</label><div>01100-555-456-789</div></div>
  <div class="field" style="top:290px;left:54px;width:420px"><label>Message</label><div>Hi, do you have a moment to talk abo...)</div></div>
</div>
<div class="abs send"><svg width="24" height="24" viewBox="0 0 24 24"><path d="M2 12L22 3 15 22 11 14z" fill="#fff"/></svg></div>

<!-- footer -->
<footer class="abs footer"></footer>
<div class="abs brand" style="top:4745px;left:130px;color:#fff;font-size:21px">Lumavex <span class="dot"></span></div>
<p class="abs footer-text">Lorem ipsum dolor sit amet, consectetur adipiscing elit, sed do eiusmod tempor incididunt ut labore et dolore</p>
<div class="abs fcol" style="left:466px"><h6>NAVIGATION</h6><ul><li>Home</li><li>Endoscope Repair</li><li>Used Endoscope</li><li>Endoscopy Systems</li></ul></div>
<div class="abs fcol" style="left:706px"><h6>RESOURCES</h6><ul><li>Endoscopy Accesories</li><li>Purchase</li><li>Contact Us</li></ul></div>
<div class="abs fcol" style="left:910px"><h6>FOLLOW US</h6><div class="social"><span></span><span></span><span></span><span></span></div></div>
<div class="abs copy">© 2022 Lumavex GmbH</div>

</body>
</html>
```